Business Card Design

Electronic Security Installation Specialists

Check out our website at www.tallbrookllc.com to see what we do.

Industry/Entity Type

Business

Contact Information for Business Card

Tall Brook
Marjorie Hadley
281 Orchard Rise
Mapleton, WV 25871

Colors
3176b5
0455a3
ffffff

```html
<!DOCTYPE html>
<html lang="en">
<head>
<meta charset="utf-8">
<title>Tall Brook – Business Card</title>
<link href="https://fonts.googleapis.com/css2?family=Open+Sans:wght@400;700&display=swap" rel="stylesheet">
<style>
  :root {
    --brand-light: #3176b5;
    --brand-deep: #0455a3;
    --brand-navy: #0a3d85;
    --paper: #ffffff;
    --backdrop: #e9ecf0;
    --ink-soft: #5a86b8;
  }
  * { box-sizing: border-box; margin: 0; padding: 0; }
  html, body {
    width: 1200px; height: 913px; overflow: hidden;
    background: var(--backdrop);
    font-family: "Open Sans", Arial, sans-serif;
  }
  .canvas { position: relative; width: 1200px; height: 913px; }
  .card {
    position: absolute; width: 520px; height: 297px;
    border-radius: 4px; overflow: hidden;
    box-shadow: 0 10px 24px rgba(0,0,0,0.18);
  }
  /* Front */
  .card-front {
    left: 70px; top: 110px;
    background: linear-gradient(135deg, var(--brand-light) 0%, var(--brand-deep) 70%, var(--brand-navy) 100%);
  }
  .card-front .swoosh { position: absolute; inset: 0; }
  .front-mark {
    position: absolute; left: 50%; top: 50%; transform: translate(-50%, -50%);
    display: flex; align-items: center; gap: 14px;
  }
  .mark-dot {
    width: 26px; height: 26px; border-radius: 50%; background: var(--paper);
  }
  .front-name {
    color: var(--paper); font-weight: 700; font-size: 40px; letter-spacing: 1px;
  }
  /* Back */
  .card-back { left: 610px; top: 500px; background: var(--paper); }
  .card-back .bands { position: absolute; inset: 0; }
  .person { position: absolute; right: 34px; top: 30px; text-align: right; }
  .person-name { color: var(--brand-light); font-weight: 700; font-size: 17px; }
  .person-role { color: var(--ink-soft); font-size: 11px; margin-top: 1px; }
  .back-mark {
    position: absolute; left: 40px; top: 96px;
    display: flex; align-items: center; gap: 10px;
  }
  .back-mark .mark-dot { background: var(--brand-deep); width: 20px; height: 20px; }
  .back-name { color: var(--brand-deep); font-weight: 700; font-size: 30px; letter-spacing: 0.5px; }
  .contacts {
    position: absolute; left: 16px; bottom: 10px; list-style: none;
    color: var(--paper); font-size: 11px; line-height: 17px;
  }
  .contacts li { display: flex; align-items: center; gap: 7px; }
  .contacts svg { width: 10px; height: 10px; fill: var(--paper); flex: none; }
  .website {
    position: absolute; right: 22px; top: 190px;
    color: var(--paper); font-size: 11px;
  }
</style>
</head>
<body>
<main class="canvas">
  <section class="card card-front" aria-label="Card front">
    <svg class="swoosh" viewBox="0 0 520 297" preserveAspectRatio="none" aria-hidden="true">
      <path d="M-20 250 C 150 170, 330 130, 540 60" fill="none" stroke="rgba(255,255,255,0.12)" stroke-width="26"/>
      <path d="M-20 40 C 180 60, 360 120, 540 240" fill="none" stroke="rgba(255,255,255,0.07)" stroke-width="18"/>
    </svg>
    <div class="front-mark">
      <span class="mark-dot"></span>
      <span class="front-name">Tall Brook</span>
    </div>
  </section>

  <section class="card card-back" aria-label="Card back">
    <svg class="bands" viewBox="0 0 520 297" preserveAspectRatio="none" aria-hidden="true">
      <path d="M300 150 C 380 150, 450 140, 520 120" fill="none" stroke="rgba(0,0,0,0.05)" stroke-width="16"/>
      <polygon points="300,176 520,176 520,297 300,297" fill="var(--brand-light)"/>
      <polygon points="0,226 270,226 280,196 345,208 345,297 0,297" fill="var(--brand-deep)"/>
    </svg>
    <div class="person">
      <p class="person-name">Marjorie Hadley</p>
      <p class="person-role">Managing Director</p>
    </div>
    <div class="back-mark">
      <span class="mark-dot"></span>
      <span class="back-name">Tall Brook</span>
    </div>
    <ul class="contacts">
      <li><svg viewBox="0 0 10 10"><path d="M2 0.5 L3.6 0.5 L4.2 2.8 L3.2 3.6 Q4 5.6 6.4 6.8 L7.2 5.8 L9.5 6.4 L9.5 8 Q9.5 9.5 8 9.5 Q1 9 0.5 2 Q0.5 0.5 2 0.5Z"/></svg>304-555-0187</li>
      <li><svg viewBox="0 0 10 10"><path d="M0 2 H10 V8.5 H0Z M0.6 2.4 L5 5.8 L9.4 2.4" stroke="var(--brand-deep)" stroke-width="0.8"/></svg>m.hadley@tallbrookllc.com</li>
      <li><svg viewBox="0 0 10 10"><path d="M5 0 A3.4 3.4 0 0 1 8.4 3.4 C8.4 6 5 10 5 10 C5 10 1.6 6 1.6 3.4 A3.4 3.4 0 0 1 5 0Z M5 2.1 A1.3 1.3 0 1 0 5 4.7 A1.3 1.3 0 1 0 5 2.1Z"/></svg>281 Orchard Rise Mapleton, WV 25871</li>
    </ul>
    <p class="website">www.tallbrookllc.com</p>
  </section>
</main>
</body>
</html>
```